Application page web design and internal pages

Create a web site where home
Page looks like an application screen for a mobile phone

Use bold icons and colors with images that have round edges

PorlenPurse Apps is name of page

Search bar at the top

Use colors from Vextaro.org for background

Price of ZORBS in top right corner (https://www.quelvix.example/trade/en-US?symbol=ZORBS_USDT&layout=basic&theme=dark)

Pages within each app should be the same color as the icon

Use the following as app icons on the page:
Key
Icon name: first screen; second screen (text)

⁃ Balances: enter pin; display balances (Your account can hold multiple currency denominations. Your balances are: ZORBS 1234567890)
⁃ Transactions: enter pin; display transactions (Your last 5 payments are ZORBS 10 from Vextaro)
⁃ Send Money: enter phone number, enter amount, send button; display message
⁃ Create Account: choose country code, enter phone number, create button; enter pin; display message ( (phone number) will be notified when their account has been created)
⁃ My Wallet Address: enter pin; display public key (IMPORTANT Send only STELLAR blockchain tokens to this deposit address: GDXQ7PLM2ZNVA9TRK4WSEY8HCBUJ6FOGDLIXP3QM5RTVKNAWZEHOBCYS)
⁃ Private Message: enter phone number, enter message, choose image, send button; enter pin; display message ( (phone number) will be notified when their message has been created)
⁃ Buy Cryptocurrency: drop drown menu of cryptocurrency to purchase (Bitcoin/Ethereum/Stellar/ZORBS), Amount in USD field, amount in chosen cryptocurrency displayed, frequency drop down menu (once/daily/weekly/monthly), buy button; enter card information (name, card number, expiration date, cvv, billing address, zip code), confirm buy button, transactions will appear on your billing statement as VEXTARO; enter pin screen; display message (You will be notified when your coin is received)
⁃ NFTs: upload image, title, description, link media, create NFT button; enter pin screen; display message (You will be notified when your NFT is created)
⁃ Earn: display message (Earn cryptocurrency doing what you do everyday, coming soon)
⁃ Files/Vault: display message (Storage for your photos, documents and more, coming soon)
⁃ Wealth: display message (Build wealth by working with a financial professional to get you to the next level), check box (I would like a financial professional to contact me about building wealth), contact me button; display message (A financial professional will contact you to achieve your financial goals)
⁃ Education: display message (Learn more about everything, coming soon)
⁃ News: display message (News from around the world, coming soon)
⁃ FAQs: use FAQs from this link https://vextaro.example/faq
⁃ Contact Us: enter message, send button; display message (Thank you for reaching out. We will reply to your message in the order it was received. Your patience is appreciated. Blessings.)

Requirements
Must have
• Application home page that looks like the Home Screen of a mobile phone
Nice to have
• Colorful icons

```html
<!DOCTYPE html>
<html lang="en">
<head>
<meta charset="utf-8">
<title>PorlenPurse Apps – Home Screens</title>
<link href="https://fonts.googleapis.com/css2?family=Poppins:wght@400;500;600&display=swap" rel="stylesheet">
<style>
  :root{
    --canvas:#f2f2f2;
    --night:#000000;
    --paper:#ffffff;
    --navy:#1c2350;
    --navy-deep:#141a3c;
    --teal:#1f8c9a;
    --teal-dark:#0f4f63;
    --ink:#1b1b1b;
    --ink-soft:#333a4a;
    --light-text:#ffffff;
    --tile-shadow:rgba(20,26,60,.18);
  }
  *{box-sizing:border-box;margin:0;padding:0}
  html,body{width:674px;height:1200px;overflow:hidden}
  body{background:var(--canvas);font-family:"Poppins",sans-serif;position:relative}
  .screen{position:absolute;width:270px;height:540px;border-radius:26px;overflow:hidden}
  .screen--dark{background:var(--night);color:var(--light-text)}
  .screen--light{background:var(--paper);color:var(--ink)}
  .pos-a{left:50px;top:30px}
  .pos-b{left:354px;top:30px}
  .pos-c{left:50px;top:610px}
  .pos-d{left:354px;top:610px}

  .header-wave{position:absolute;left:0;top:0;width:270px;height:130px}
  .header-wave--light{height:160px}
  .brand{position:absolute;top:62px;left:0;right:0;display:flex;align-items:center;justify-content:center;gap:6px;
    font-size:12px;font-weight:500;letter-spacing:.8px;color:var(--light-text);z-index:1}
  .brand__mark{width:9px;height:9px;border:1.5px solid currentColor;border-radius:2px}
  .price-bar{position:absolute;top:100px;left:30px;right:30px;height:30px;border-radius:5px;background:var(--navy);
    display:flex;align-items:center;justify-content:space-between;padding:0 10px;font-size:8.5px;color:var(--light-text)}
  .price-bar__coin::after{content:"⌄";margin-left:5px;position:relative;top:-2px}
  .price-bar__value{display:flex;align-items:center;gap:5px}
  .price-bar__value::before{content:"";width:7px;height:7px;border-radius:2px;background:#3e7fd6}
  .search{position:absolute;top:150px;left:40px;right:40px;height:22px;border-radius:3px;background:var(--paper);
    border:1px solid #c7cad6;display:flex;align-items:center;padding-left:7px;font-size:6.5px;color:#7b7f8c}
  .search__button{position:absolute;right:-1px;top:-1px;width:22px;height:22px;border-radius:3px;background:var(--navy);display:flex;align-items:center;justify-content:center}

  .app-grid{position:absolute;left:18px;right:18px;display:grid;grid-template-columns:repeat(4,1fr);row-gap:16px}
  .app-grid--home{top:196px}
  .app-grid--more{top:40px}
  .app{display:flex;flex-direction:column;align-items:center;gap:5px;font-size:5.5px;text-align:center;white-space:nowrap}
  .app__tile{width:44px;height:44px;border-radius:8px;display:flex;align-items:center;justify-content:center}
  .screen--dark .app__tile{background:#f4f4f4}
  .screen--light .app__tile{background:var(--paper);box-shadow:0 3px 8px var(--tile-shadow)}
  .app__art{width:32px;height:32px;border-radius:8px}
  .art-balances{background:linear-gradient(135deg,#f0a23a,#8a4b1c)}
  .art-transactions{background:linear-gradient(135deg,#f5d34a,#3c8de0)}
  .art-send{background:linear-gradient(135deg,#ffc04a,#ec6a2b)}
  .art-account{background:linear-gradient(135deg,#f7c53a,#f07b2d)}
  .art-address{background:linear-gradient(135deg,#e0463b,#f5b23a)}
  .art-message{background:linear-gradient(135deg,#3d6fe0,#c24fd9)}
  .art-buy{background:linear-gradient(135deg,#f5c23a,#2b74d6)}
  .art-nft{background:radial-gradient(circle,#c98d4a,#6e4220)}
  .art-earn{background:linear-gradient(135deg,#7a4a22,#3b2210)}
  .art-vault{background:linear-gradient(135deg,#7fb4f0,#2a5cc0)}
  .art-wealth{background:linear-gradient(135deg,#f7d04a,#e9781e)}
  .art-education{background:linear-gradient(135deg,#3b7fe0,#f2c23a)}
  .art-news{background:linear-gradient(135deg,#e9e9ee,#f0a63a)}
  .art-faq{background:linear-gradient(135deg,#ee4b7a,#3a7be0)}
  .art-contact{background:linear-gradient(135deg,#2d3a8c,#f3b43a)}
  .art-claim{background:linear-gradient(135deg,#f2c43a,#e9562e)}
  .art-card{background:linear-gradient(135deg,#3a8de0,#f0b53a)}
  .art-shop{background:linear-gradient(135deg,#e5332a,#f7c23a)}

  .policy{position:absolute;bottom:48px;left:0;right:0;text-align:center;font-size:5.5px;color:var(--light-text)}
  .screen--light .policy{color:var(--ink-soft)}
  .nav-bar{position:absolute;left:0;right:0;bottom:0;height:40px;background:var(--navy-deep);display:flex;align-items:center;justify-content:center}
</style>
</head>
<body>

<!-- Dark home -->
<section class="screen screen--dark pos-a">
  <svg class="header-wave" viewBox="0 0 270 130" aria-hidden="true">
    <defs><linearGradient id="waveDark" x1="0" y1="0" x2="1" y2="1"><stop offset="0" stop-color="#1f8c9a"/><stop offset="1" stop-color="#0c2f45"/></linearGradient></defs>
    <path d="M0 0H270V40C210 10 150 20 120 60C95 95 50 120 0 125Z" fill="url(#waveDark)"/>
    <path d="M270 40C210 10 150 20 120 60C95 95 50 120 0 125V130C55 126 100 100 126 64C155 26 212 18 270 48Z" fill="#ffffff"/>
  </svg>
  <div class="brand"><span class="brand__mark"></span>PORLENPURSE</div>
  <div class="price-bar"><span class="price-bar__coin">ZORBS</span><span class="price-bar__value">$ 5.00</span></div>
  <div class="search">Search Here<span class="search__button"><svg width="10" height="10" viewBox="0 0 10 10"><circle cx="4" cy="4" r="3" fill="none" stroke="#fff" stroke-width="1.2"/><path d="M6.3 6.3L9 9" stroke="#fff" stroke-width="1.2"/></svg></span></div>
  <div class="app-grid app-grid--home">
    <div class="app"><div class="app__tile"><div class="app__art art-balances" role="img" aria-label="Balances icon: wallet with coins"></div></div>Balances</div>
    <div class="app"><div class="app__tile"><div class="app__art art-transactions" role="img" aria-label="Transactions icon: receipt list"></div></div>Transactions</div>
    <div class="app"><div class="app__tile"><div class="app__art art-send" role="img" aria-label="Send Money icon: coins with arrow"></div></div>Send Money</div>
    <div class="app"><div class="app__tile"><div class="app__art art-account" role="img" aria-label="Create Account icon: person with plus"></div></div>Create Account</div>
    <div class="app"><div class="app__tile"><div class="app__art art-address" role="img" aria-label="Wallet Address icon: location card"></div></div>Wallet Address</div>
    <div class="app"><div class="app__tile"><div class="app__art art-message" role="img" aria-label="Private Message icon: chat bubble with lock"></div></div>Private Message</div>
    <div class="app"><div class="app__tile"><div class="app__art art-buy" role="img" aria-label="Buy Cryptocurrency icon: coin and cart"></div></div>Buy Cryptocurrency</div>
    <div class="app"><div class="app__tile"><div class="app__art art-nft" role="img" aria-label="NFTs icon: digital coin"></div></div>NFTs</div>
    <div class="app"><div class="app__tile"><div class="app__art art-earn" role="img" aria-label="Earn icon: money bag"></div></div>Earn</div>
    <div class="app"><div class="app__tile"><div class="app__art art-vault" role="img" aria-label="Files and Vault icon: folder safe"></div></div>Files/Vault</div>
    <div class="app"><div class="app__tile"><div class="app__art art-wealth" role="img" aria-label="Wealth icon: growing coin stack"></div></div>Wealth</div>
    <div class="app"><div class="app__tile"><div class="app__art art-education" role="img" aria-label="Education icon: graduation cap"></div></div>Education</div>
    <div class="app"><div class="app__tile"><div class="app__art art-card" role="img" aria-label="App icon"></div></div></div>
    <div class="app"><div class="app__tile"><div class="app__art art-faq" role="img" aria-label="App icon"></div></div></div>
    <div class="app"><div class="app__tile"><div class="app__art art-contact" role="img" aria-label="App icon"></div></div></div>
    <div class="app"><div class="app__tile"><div class="app__art art-claim" role="img" aria-label="App icon"></div></div></div>
  </div>
  <nav class="nav-bar"><svg width="14" height="13" viewBox="0 0 14 13"><path d="M7 0L14 6H12V13H8.5V9H5.5V13H2V6H0Z" fill="#fff"/></svg></nav>
</section>

<!-- Dark second page -->
<section class="screen screen--dark pos-b">
  <div class="app-grid app-grid--more">
    <div class="app"><div class="app__tile"><div class="app__art art-news" role="img" aria-label="News icon: newspaper"></div></div>News</div>
    <div class="app"><div class="app__tile"><div class="app__art art-faq" role="img" aria-label="FAQs icon: question bubbles"></div></div>FAQs</div>
    <div class="app"><div class="app__tile"><div class="app__art art-contact" role="img" aria-label="Contact Us icon: headset"></div></div>Contact Us</div>
    <div class="app"><div class="app__tile"><div class="app__art art-claim" role="img" aria-label="Claim icon: hand with coin"></div></div>Claim</div>
    <div class="app"><div class="app__tile"><div class="app__art art-card" role="img" aria-label="Debit Card icon: payment card"></div></div>Debit Card</div>
    <div class="app"><div class="app__tile"><div class="app__art art-shop" role="img" aria-label="App Shop icon: shopping bag"></div></div>App Shop</div>
  </div>
  <p class="policy">©Vextaro. Our Loyalty Transaction Policy</p>
  <nav class="nav-bar"><svg width="14" height="13" viewBox="0 0 14 13"><path d="M7 0L14 6H12V13H8.5V9H5.5V13H2V6H0Z" fill="#fff"/></svg></nav>
</section>

<!-- Light home -->
<section class="screen screen--light pos-c">
  <svg class="header-wave header-wave--light" viewBox="0 0 270 160" aria-hidden="true">
    <defs><linearGradient id="waveLight" x1="0" y1="0" x2="1" y2="1"><stop offset="0" stop-color="#1f8c9a"/><stop offset="1" stop-color="#0c2f45"/></linearGradient></defs>
    <path d="M0 0H270V120C220 150 170 128 120 138C80 146 40 150 0 142Z" fill="url(#waveLight)"/>
  </svg>
  <div class="brand"><span class="brand__mark"></span>PORLENPURSE</div>
  <div class="price-bar"><span class="price-bar__coin">ZORBS</span><span class="price-bar__value">$ 5.00</span></div>
  <div class="search">Search Here<span class="search__button"><svg width="10" height="10" viewBox="0 0 10 10"><circle cx="4" cy="4" r="3" fill="none" stroke="#fff" stroke-width="1.2"/><path d="M6.3 6.3L9 9" stroke="#fff" stroke-width="1.2"/></svg></span></div>
  <div class="app-grid app-grid--home">
    <div class="app"><div class="app__tile"><div class="app__art art-balances" role="img" aria-label="Balances icon: wallet with coins"></div></div>Balances</div>
    <div class="app"><div class="app__tile"><div class="app__art art-transactions" role="img" aria-label="Transactions icon: receipt list"></div></div>Transactions</div>
    <div class="app"><div class="app__tile"><div class="app__art art-send" role="img" aria-label="Send Money icon: coins with arrow"></div></div>Send Money</div>
    <div class="app"><div class="app__tile"><div class="app__art art-account" role="img" aria-label="Create Account icon: person with plus"></div></div>Create Account</div>
    <div class="app"><div class="app__tile"><div class="app__art art-address" role="img" aria-label="Wallet Address icon: location card"></div></div>Wallet Address</div>
    <div class="app"><div class="app__tile"><div class="app__art art-message" role="img" aria-label="Private Message icon: chat bubble with lock"></div></div>Private Message</div>
    <div class="app"><div class="app__tile"><div class="app__art art-buy" role="img" aria-label="Buy Cryptocurrency icon: coin and cart"></div></div>Buy Cryptocurrency</div>
    <div class="app"><div class="app__tile"><div class="app__art art-nft" role="img" aria-label="NFTs icon: digital coin"></div></div>NFTs</div>
    <div class="app"><div class="app__tile"><div class="app__art art-earn" role="img" aria-label="Earn icon: money bag"></div></div>Earn</div>
    <div class="app"><div class="app__tile"><div class="app__art art-vault" role="img" aria-label="Files and Vault icon: folder safe"></div></div>Files/Vault</div>
    <div class="app"><div class="app__tile"><div class="app__art art-wealth" role="img" aria-label="Wealth icon: growing coin stack"></div></div>Wealth</div>
    <div class="app"><div class="app__tile"><div class="app__art art-education" role="img" aria-label="Education icon: graduation cap"></div></div>Education</div>
    <div class="app"><div class="app__tile"><div class="app__art art-card" role="img" aria-label="App icon"></div></div></div>
    <div class="app"><div class="app__tile"><div class="app__art art-faq" role="img" aria-label="App icon"></div></div></div>
    <div class="app"><div class="app__tile"><div class="app__art art-contact" role="img" aria-label="App icon"></div></div></div>
    <div class="app"><div class="app__tile"><div class="app__art art-claim" role="img" aria-label="App icon"></div></div></div>
  </div>
  <nav class="nav-bar"><svg width="14" height="13" viewBox="0 0 14 13"><path d="M7 0L14 6H12V13H8.5V9H5.5V13H2V6H0Z" fill="#fff"/></svg></nav>
</section>

<!-- Light second page -->
<section class="screen screen--light pos-d">
  <div class="app-grid app-grid--more">
    <div class="app"><div class="app__tile"><div class="app__art art-news" role="img" aria-label="News icon: newspaper"></div></div>News</div>
    <div class="app"><div class="app__tile"><div class="app__art art-faq" role="img" aria-label="FAQs icon: question bubbles"></div></div>FAQs</div>
    <div class="app"><div class="app__tile"><div class="app__art art-contact" role="img" aria-label="Contact Us icon: headset"></div></div>Contact Us</div>
    <div class="app"><div class="app__tile"><div class="app__art art-claim" role="img" aria-label="Claim icon: hand with coin"></div></div>Claim</div>
    <div class="app"><div class="app__tile"><div class="app__art art-card" role="img" aria-label="Debit Card icon: payment card"></div></div>Debit Card</div>
    <div class="app"><div class="app__tile"><div class="app__art art-shop" role="img" aria-label="App Shop icon: shopping bag"></div></div>App Shop</div>
  </div>
  <p class="policy">©Vextaro. Our Loyalty Transaction Policy</p>
  <nav class="nav-bar"><svg width="14" height="13" viewBox="0 0 14 13"><path d="M7 0L14 6H12V13H8.5V9H5.5V13H2V6H0Z" fill="#fff"/></svg></nav>
</section>

</body>
</html>
```